BrivoTerna. Lantern of the Steady Harvest. Business card

Professional business card for BrivoTerna (Lantern of the Steady Harvest)
My rationale: Strategy-> Execution-> Results-> Value that lead to the BrivoTerna name: We put the Lantern of the Steady Harvest.
We deliver value to our customers helping them at defining a good strategy (cyan arrow). 90% of well formulated strategies fail due to poor execution so we also consider strategical execution very important (green arrow). Due to the execution we obtain the results (blue arrow). Finally, the results provide feedback to redefine strategy, and the new strategy has to be executed and new results obtained providing new feedback and on and on. It's like a wheel that finally, must create corporate value: value for shareholders, staholders, employees, providers...-

Target Market(s)

CEOs and steering comitees , invewrnent funds

Industry/Entity Type

Business Consultant

Contact Information for Business Card

Teodoro Vinsquel
CEO & Founder
teodoro.vinsquel@brivoterna-example.com
Mobile: +34 655.803.912
www.brivoterna-example.com

Colors

Designer to choose colors to be used in the design.

Requirements
Nice to have
• Nice to hace the words: Strategy, execution, results
• Nice to vave the claim: Lantern of the Steady Harvest
• The three colors should be shown:
• cyan for STRATEGY
• green for EXECUTION
• blue for RESULTS
Should not have
• Complete black background

```html
<!DOCTYPE html>
<html lang="en">
<head>
<meta charset="utf-8">
<title>BrivoTerna – Business Card</title>
<link href="https://fonts.googleapis.com/css2?family=Signika:wght@600&family=Roboto:wght@400;500;700&display=swap" rel="stylesheet">
<style>
  :root {
    --page-bg: #ecebe8;
    --navy: #233a8f;
    --royal: #22449a;
    --sky: #2a8fd0;
    --cyan: #2aa6df;
    --white: #ffffff;
    --ink: #2b2b2b;
  }
  * { margin: 0; padding: 0; box-sizing: border-box; }
  html, body { width: 1200px; height: 900px; overflow: hidden; }
  body { background: var(--page-bg); position: relative; font-family: "Roboto", Arial, sans-serif; }

  .card {
    position: absolute;
    left: 311px;
    width: 577px;
    height: 329px;
    overflow: hidden;
    box-shadow: 0 4px 14px rgba(0,0,0,0.22);
  }

  /* Front */
  .card-front {
    top: 98px;
    background: linear-gradient(100deg, var(--sky) 0%, #2a78c4 45%, var(--royal) 100%);
    color: var(--white);
    text-align: center;
  }
  .front-name {
    position: absolute;
    left: 0; right: 0; top: 170px;
    font-family: "Signika", "Arial Narrow", sans-serif;
    font-weight: 600;
    font-size: 46px;
    letter-spacing: -0.5px;
  }
  .front-claim {
    position: absolute;
    left: 0; right: 0; top: 224px;
    font-weight: 500;
    font-size: 15px;
    letter-spacing: 0.6px;
    text-transform: uppercase;
  }
  .front-pillars {
    position: absolute;
    left: 0; right: 0; top: 246px;
    font-weight: 500;
    font-size: 14px;
    letter-spacing: 0.8px;
    text-transform: uppercase;
  }
  .front-pillars span { padding: 0 6px; }

  /* Back */
  .card-back { top: 472px; background: var(--white); }
  .back-band { position: absolute; inset: 0; }
  .back-name {
    position: absolute;
    left: 32px; top: 32px;
    font-family: "Signika", "Arial Narrow", sans-serif;
    font-weight: 600;
    font-size: 40px;
    color: var(--navy);
    letter-spacing: -0.5px;
  }
  .person {
    position: absolute;
    right: 31px; top: 40px;
    text-align: right;
  }
  .person-name { font-weight: 700; font-size: 15px; color: var(--navy); letter-spacing: 0.5px; }
  .person-role { font-size: 11px; color: var(--ink); letter-spacing: 0.3px; margin-top: 1px; }

  .contacts {
    position: absolute;
    left: 31px; top: 225px;
    list-style: none;
    color: var(--white);
    font-size: 13px;
  }
  .contacts li { display: flex; align-items: center; height: 24px; }
  .contacts svg { width: 16px; height: 16px; margin-right: 8px; fill: var(--white); }
</style>
</head>
<body>

<section class="card card-front" aria-label="Card front">
  <h1 class="front-name">BrivoTerna</h1>
  <p class="front-claim">Lantern of the Steady Harvest</p>
  <p class="front-pillars"><span>Strategy</span>|<span>Execution</span>|<span>Results</span></p>
</section>

<section class="card card-back" aria-label="Card back">
  <svg class="back-band" viewBox="0 0 577 329" aria-hidden="true">
    <defs>
      <linearGradient id="bandFill" x1="0" y1="0" x2="1" y2="0">
        <stop offset="0" stop-color="#22449a"/>
        <stop offset="0.55" stop-color="#2a78c4"/>
        <stop offset="1" stop-color="#2aa6df"/>
      </linearGradient>
    </defs>
    <path d="M0 180 Q290 164 577 198 L577 329 L0 329 Z" fill="url(#bandFill)"/>
  </svg>

  <h2 class="back-name">BrivoTerna</h2>

  <div class="person">
    <p class="person-name">TEODORO VINSQUEL</p>
    <p class="person-role">CEO &amp; FOUNDER</p>
  </div>

  <ul class="contacts">
    <li>
      <svg viewBox="0 0 16 16" aria-hidden="true"><path d="M4 0h8a1.5 1.5 0 0 1 1.5 1.5v13A1.5 1.5 0 0 1 12 16H4a1.5 1.5 0 0 1-1.5-1.5v-13A1.5 1.5 0 0 1 4 0zm0.5 2v10h7V2zm3.5 11a1 1 0 1 0 0 2 1 1 0 0 0 0-2z"/></svg>
      +34 655.803.912
    </li>
    <li>
      <svg viewBox="0 0 16 16" aria-hidden="true"><path d="M0 3h16v10H0zm1.5 1.3v.3L8 9l6.5-4.4v-.3zm0 2.1v5.1h13V6.4L8 10.8z"/></svg>
      teodoro.vinsquel@brivoterna-example.com
    </li>
    <li>
      <svg viewBox="0 0 16 16" aria-hidden="true"><path d="M8 0a8 8 0 1 0 0 16A8 8 0 0 0 8 0zm-1 2c-1 1-1.5 2-1 3s2 1 2 2-1 1.5-1 2.5S8 11 7 13c-.5 1-2 0-2.5-1S4 10 3 9 2 6 3 4.5 6 2 7 2zm3 1c1.5.3 3 1.5 3.5 3s-1 1-2 1.5-1 2-2 2-1-1-1-2 .5-1.5 1-2-.5-1.5 0-2.5z"/></svg>
      www.brivoterna-example.com
    </li>
  </ul>
</section>

</body>
</html>
```